Stage Design Company Business Card

We are looking to step up up our business card design for our team.

We are a Full service Design and Consultation company for Stage and TV with an emphasis in Theatrical Lighting.

We like our materials to be clean and modern with solid colors free of patterns and gradients. Our brand consists of 4 primary colors Purple, Black, Grey, and White. Provided is our Word Mark as well as our Symbol Logo.

We would like our cards to leave an impression beyond the information, show our attention to design and detail, and make our marks an easily recognized feature (together or apart) for our clients.

We need a warm approachable comfortable feel for some clients, and a professional flair for the board member type clients.

Attached are our brand elements, and our existing cards to give a sense of our style and a glipse at the information we provide on our cards.

Target Market(s)

broad client base from church leaders to high school teachers and architects.

Industry/Entity Type

Business

Contact Information for Business Card

We format our phone number with periods not parenthesis or dashes. Information will be edited for each of our team members, and team member specific cards are not part of this scope, but rather a template so to speak.

Font styles to use
Sans Serif

Colors
6b449b
ffffff
000000
333333
aaaaaa

Requirements
Must have
• Wordmark and logo mark present (does not need to exist on the same side of card)
• Brand Colors,
• Name, Phone, Email, Address.
• Unique choices that make someone stop and take a second look
Nice to have
• It would be nice to somehow convey what we DO, as our brand name does not lend itself to this, outside of an obvious tagline though.....
• social media if not crowded. all of our handles match (instagram, twitter, facebook)
Should not have
• "clipart"

```html
<!DOCTYPE html>
<html lang="en">
<head>
<meta charset="utf-8">
<title>Halden Stageworks – Business Card</title>
<link rel="stylesheet" href="https://fonts.googleapis.com/css2?family=Jost:wght@400;500;600&display=swap">
<style>
  :root {
    --purple: #3f2a78;
    --ink: #333333;
    --grey: #aaaaaa;
    --card: #ffffff;
    --backdrop: #8e8d8e;
  }
  * { margin: 0; padding: 0; box-sizing: border-box; }
  html, body {
    width: 1200px; height: 929px; overflow: hidden;
    background: var(--backdrop);
    font-family: "Jost", "Futura", sans-serif;
  }
  .stage { position: relative; width: 1200px; height: 929px; }
  .card {
    position: absolute; left: 250px; width: 700px; height: 400px;
    background: var(--card);
    box-shadow: 0 6px 18px rgba(0,0,0,0.25);
  }
  .card--front { top: 50px; }
  .card--back { top: 480px; }

  /* Front */
  .brand {
    position: absolute; left: 0; right: 0; top: 110px;
    display: flex; flex-direction: column; align-items: center;
  }
  .brand__dot {
    width: 70px; height: 70px; border-radius: 50%;
    background: var(--purple); margin-bottom: 30px;
  }
  .brand__name {
    color: var(--purple); font-weight: 500; font-size: 26px;
    letter-spacing: 14px; text-transform: uppercase;
    text-align: center; line-height: 1.5; padding-left: 14px;
  }
  .brand__name span { display: block; font-size: 12px; letter-spacing: 8px; padding-left: 8px; }

  /* Back */
  .person {
    position: absolute; right: 375px; top: 150px; text-align: right;
  }
  .person__name {
    color: var(--purple); font-weight: 600; font-size: 25px;
    letter-spacing: 0.5px; text-transform: uppercase; line-height: 1.1;
  }
  .person__role { color: var(--ink); font-size: 16px; margin-top: 2px; }
  .divider {
    position: absolute; left: 340px; top: 135px; width: 1.5px; height: 80px;
    background: var(--purple);
  }
  .contacts {
    position: absolute; left: 360px; top: 130px; list-style: none;
    color: var(--ink); font-size: 15.5px; line-height: 28px;
  }
  .contacts li { display: flex; align-items: center; gap: 10px; }
  .contacts svg { width: 12px; height: 12px; flex: none; }
  .address {
    position: absolute; left: 0; right: 0; top: 305px; text-align: center;
    color: var(--ink); font-size: 15px; letter-spacing: 0.5px; padding-left: 60px;
  }
</style>
</head>
<body>
<main class="stage">
  <section class="card card--front" aria-label="Card front">
    <div class="brand">
      <div class="brand__dot"></div>
      <p class="brand__name">Halden<span>Stageworks</span></p>
    </div>
  </section>

  <section class="card card--back" aria-label="Card back">
    <div class="person">
      <p class="person__name">Marcus L Reed</p>
      <p class="person__role">Owner</p>
    </div>
    <div class="divider"></div>
    <ul class="contacts">
      <li>
        <svg viewBox="0 0 12 12" aria-hidden="true"><rect x="3" y="0.8" width="6" height="10.4" rx="1" fill="none" stroke="#3f2a78" stroke-width="1.3"/></svg>
        800.555.0142
      </li>
      <li>
        <svg viewBox="0 0 12 12" aria-hidden="true"><rect x="0.5" y="2" width="11" height="8" fill="#3f2a78"/><path d="M0.5 2 L6 6.5 L11.5 2" fill="none" stroke="#fff" stroke-width="1.1"/></svg>
        info@halden-st.com
      </li>
      <li>
        <svg viewBox="0 0 12 12" aria-hidden="true"><circle cx="5" cy="5" r="3.6" fill="none" stroke="#3f2a78" stroke-width="1.6"/><line x1="7.6" y1="7.6" x2="11.2" y2="11.2" stroke="#3f2a78" stroke-width="1.8"/></svg>
        halden-st.com
      </li>
    </ul>
    <p class="address">52 E. Oak ST Tempe, AZ 85281</p>
  </section>
</main>
</body>
</html>
```